Tolbek cards

I want a simple business card that pops.
Logo on one side.
On side two i want.
"Are you thinking about a new building on your property, or renovating an existing structure? Contact".....
Owners Name: Dale Whitacre
Owners Phone number: 610-555-0187
Address:4076 Copper Ridge RD, Kessford, PA 16842
Committed to Quality, Service, and Integrity

```html
<!DOCTYPE html>
<html lang="en">
<head>
<meta charset="utf-8">
<title>Tolbek Builders LLC – Business Card</title>
<link rel="stylesheet" href="https://fonts.googleapis.com/css2?family=Montserrat:wght@400;500;600;700;800&display=swap">
<style>
  :root {
    --canvas: #979797;
    --brown-deep: #412c1a;
    --brown-mid: #5a4029;
    --brown-accent: #6b4a30;
    --brown-soft: #9a7a5a;
    --ink: #2b2b2b;
    --paper: #ffffff;
  }
  * { box-sizing: border-box; margin: 0; padding: 0; }
  html, body {
    width: 1200px; height: 1108px; overflow: hidden;
    background: var(--canvas);
    font-family: "Montserrat", sans-serif;
  }
  .canvas { position: relative; width: 1200px; height: 1108px; }

  .card {
    position: absolute; left: 242px; width: 715px;
    border-radius: 30px; overflow: hidden;
  }

  /* Front side */
  .card--front {
    top: 119px; height: 408px;
    background:
      linear-gradient(115deg, transparent 38%, rgba(255,255,255,0.08) 48%, rgba(255,255,255,0.04) 62%, transparent 72%),
      var(--brown-deep);
    display: flex; align-items: center; justify-content: center;
  }
  .front-name {
    font-weight: 700; font-size: 64px; letter-spacing: 2px;
    color: var(--brown-soft);
  }

  /* Back side */
  .card--back { top: 580px; height: 408px; background: var(--paper); }
  .back-intro {
    position: absolute; top: 22px; left: 0; right: 0;
    text-align: center; font-size: 18px; line-height: 29px;
    color: var(--ink); letter-spacing: 0.3px;
  }
  .back-brand {
    position: absolute; left: 70px; top: 175px; width: 240px;
    text-align: center; color: var(--brown-deep); font-weight: 800;
  }
  .back-brand__name { display: block; font-size: 50px; line-height: 1; letter-spacing: 1px; text-transform: uppercase; }
  .back-brand__sub { display: block; font-size: 17px; margin-top: 8px; letter-spacing: 1px; text-transform: uppercase; }
  .back-divider {
    position: absolute; left: 348px; top: 117px; width: 2px; height: 175px;
    background: var(--brown-deep);
  }
  .contact { position: absolute; left: 386px; top: 112px; color: var(--ink); }
  .contact__name { font-size: 31px; font-weight: 700; color: var(--brown-accent); line-height: 1.1; }
  .contact__role { font-size: 18px; margin-top: 6px; }
  .contact__address { font-size: 18px; line-height: 29px; margin-top: 20px; }
  .contact__phone { font-size: 18px; margin-top: 19px; display: flex; align-items: center; gap: 8px; }
  .contact__phone svg { width: 17px; height: 14px; fill: var(--ink); }
  .back-band {
    position: absolute; left: 0; right: 0; top: 358px; height: 25px;
    background: var(--brown-deep); color: var(--paper);
    font-size: 18px; line-height: 25px; text-align: center; letter-spacing: 0.3px;
  }
</style>
</head>
<body>
<main class="canvas">
  <section class="card card--front" aria-label="Card front">
    <span class="front-name">Tolbek</span>
  </section>

  <section class="card card--back" aria-label="Card back">
    <p class="back-intro">Are you thinking about a new building on your<br>property, or renovating an existing structure? Contact</p>

    <div class="back-brand">
      <span class="back-brand__name">Tolbek</span>
      <span class="back-brand__sub">Builders LLC</span>
    </div>

    <div class="back-divider"></div>

    <div class="contact">
      <h1 class="contact__name">Dale Whitacre</h1>
      <p class="contact__role">Owner</p>
      <p class="contact__address">4076 Copper Ridge RD,<br>Kessford, PA 16842</p>
      <p class="contact__phone">
        <svg viewBox="0 0 17 14" aria-hidden="true"><path d="M1 5c0-3 4-4 7.5-4S16 2 16 5l-3 1-1-2H5L4 6zM4 7h9l2 6H2z"/></svg>
        610-555-0187
      </p>
    </div>

    <div class="back-band">Committed to Quality, Service, and Integrity</div>
  </section>
</main>
</body>
</html>
```